Brell Stone Company Business Cards

Front and Back Business Card - logo and text setup - cool design. I need workable photoshop or illustrator files so I can setup each employee card with design that is created
Updates

Hi everyone, thank you for the great entries. Please no more white and blue cards - there are so many already - black and silver only now please. thanks!

Target Market(s)

Construction Industry - Facility Managers

Industry/Entity Type

Construction

Contact Information for Business Card

I really like contemporary simplistic looks - clean neat....not opposed to seeing some black backrounds

Requirements
Must have
• Logo/website address with design on front only - www.brellstone-example.com (logo attached)
• Back:
• Name/Title/Company Address/Phone/email address
Nice to have
• Cool design
Should not have
• Nothing gimmicky like Fire or Water - since we are a Fire Protection company - it has all been done

```html
<!DOCTYPE html>
<html lang="en">
<head>
<meta charset="utf-8">
<title>Brell Stone Company Business Cards</title>
<link href="https://fonts.googleapis.com/css2?family=Open+Sans:wght@400;600;700;800&display=swap" rel="stylesheet">
<style>
  :root {
    --page-bg: #1c1c1e;
    --card-dark: #0b0b0c;
    --card-mid: #26272a;
    --card-sheen: #3a3b3f;
    --text-light: #f2f2f2;
    --text-soft: #d4d4d6;
    --accent-red: #e8432c;
    --divider: #8a8a8e;
  }
  * { box-sizing: border-box; margin: 0; padding: 0; }
  html, body {
    width: 1200px;
    height: 960px;
    overflow: hidden;
    background: var(--page-bg);
    font-family: "Open Sans", Arial, sans-serif;
  }
  .canvas {
    width: 1200px;
    height: 960px;
    display: flex;
    flex-direction: column;
    align-items: center;
    justify-content: center;
    gap: 56px;
  }
  .card {
    position: relative;
    width: 700px;
    height: 400px;
    border-radius: 6px;
    overflow: hidden;
    background:
      linear-gradient(105deg, transparent 38%, rgba(255,255,255,0.07) 50%, transparent 62%),
      linear-gradient(75deg, transparent 58%, rgba(255,255,255,0.05) 68%, transparent 78%),
      repeating-linear-gradient(0deg, rgba(255,255,255,0.015) 0 1px, transparent 1px 3px),
      linear-gradient(160deg, var(--card-mid) 0%, var(--card-dark) 45%, var(--card-sheen) 70%, var(--card-dark) 100%);
    box-shadow: 0 18px 40px rgba(0,0,0,0.55);
  }

  /* Front */
  .card-front {
    display: flex;
    flex-direction: column;
    align-items: center;
    justify-content: center;
    gap: 34px;
  }
  .brand-name {
    font-weight: 800;
    color: var(--text-light);
    letter-spacing: -1px;
    line-height: 1;
  }
  .card-front .brand-name { font-size: 82px; }
  .front-website {
    font-size: 19px;
    letter-spacing: 4px;
    color: var(--text-soft);
  }

  /* Back */
  .card-back {
    display: flex;
    align-items: center;
    padding: 0 56px;
  }
  .back-brand {
    width: 300px;
  }
  .card-back .brand-name { font-size: 52px; }
  .contact-block {
    border-left: 1.5px solid var(--divider);
    padding: 10px 0 10px 26px;
    color: var(--text-light);
  }
  .person-name {
    font-size: 22px;
    font-weight: 700;
  }
  .person-title {
    font-size: 19px;
    margin-bottom: 18px;
  }
  .contact-line {
    display: flex;
    align-items: center;
    gap: 10px;
    font-size: 18px;
    line-height: 1.6;
  }
  .contact-icon {
    width: 16px;
    height: 16px;
    flex: none;
  }
  .address {
    margin-top: 14px;
    font-size: 18px;
    line-height: 1.4;
  }
</style>
</head>
<body>
<main class="canvas">

  <section class="card card-front" aria-label="Business card front">
    <div class="brand-name">Brell Stone</div>
    <div class="front-website">www.brellstone-example.com</div>
  </section>

  <section class="card card-back" aria-label="Business card back">
    <div class="back-brand">
      <div class="brand-name">Brell Stone</div>
    </div>
    <div class="contact-block">
      <div class="person-name">Dana Merrow</div>
      <div class="person-title">President</div>

      <div class="contact-line">
        <svg class="contact-icon" viewBox="0 0 16 16" aria-hidden="true">
          <path fill="var(--accent-red)" d="M3.6 1.2l2.2 2.6c.3.4.3.9 0 1.3L4.7 6.4c.9 2 2.5 3.6 4.5 4.6l1.3-1.1c.4-.3.9-.3 1.3 0l2.6 2.2c.4.3.4.9.1 1.3l-1.3 1.4c-.5.5-1.2.6-1.9.4C6.1 13.8 2.2 9.9.8 4.7.6 4 .8 3.3 1.2 2.8L2.3 1.2c.4-.4 1-.4 1.3 0z"/>
        </svg>
        <span>(555) 014-2087</span>
      </div>
      <div class="contact-line">
        <svg class="contact-icon" viewBox="0 0 16 16" aria-hidden="true">
          <rect x="1" y="3" width="14" height="10" rx="1" fill="var(--accent-red)"/>
          <path d="M1.5 3.8L8 9l6.5-5.2" fill="none" stroke="var(--card-dark)" stroke-width="1.3"/>
        </svg>
        <span>info@brellstone-example.com</span>
      </div>
      <div class="contact-line">
        <svg class="contact-icon" viewBox="0 0 16 16" aria-hidden="true">
          <circle cx="8" cy="8" r="7" fill="var(--accent-red)"/>
          <g fill="none" stroke="var(--card-dark)" stroke-width="1">
            <ellipse cx="8" cy="8" rx="3" ry="7"/>
            <path d="M1 8h14M2 4.5h12M2 11.5h12"/>
          </g>
        </svg>
        <span>www.brellstone-example.com</span>
      </div>

      <div class="address">
        48 Harbor Works Lane<br>
        Millbrook, NY 10999
      </div>
    </div>
  </section>

</main>
</body>
</html>
```